Local massage therapist needs some new marketing material

Hi there! I am a massage therapist here in Denver, CO in Alder Bend(shopping and art district) of the city. My business is called Lumo Bodywork of Denver. My practice has an eastern influence and I do reflexology, thai massage and use Chinese herbs, etc. I know all my clients and pay close attention to details. I am also very respectful of tradition and it shows in how I work. I tend to like modern, clean, fun, Asian designs. I am wanting a new business card and brochure. I have a logo and branding for my business that I want used in the design. Currently, the sign for my building is purple and I think my logo was designed to be purple. I will attach pictures of it and can send whatever files are necessary so it can be integrated into the brochure, etc. I like the purple but open to using other colors as well. Thanks!
My website is lumobodyworkofdenver.example where info can be gathered about me and services/fees for brochure.
Updates

Just increased budget. Please see new feedback in discussion thread.

Thanks!

                                       HEY ALL,

Just wanted to let you know that I made a change to my website. It is on the Prices Page. I no longer have the frequent  flyer prices but I added discounts. Let me know if you have any questions. Thanks so much!

Target Market(s)

healthy, urban, educated, upper middle class, yogis

Industry/Entity Type

Marketing

Requirements
Must have
• logo stays purple
Should not have
• not too busy

```html
<!DOCTYPE html>
<html lang="en">
<head>
<meta charset="utf-8">
<title>Lumo Bodywork of Denver – Business Card</title>
<link rel="stylesheet" href="https://fonts.googleapis.com/css2?family=Source+Sans+3:ital,wght@0,400;0,600;0,700;1,400&display=swap">
<style>
  :root {
    --purple: #662d91;
    --charcoal: #3d3d3d;
    --text: #4a4a4a;
    --rule: #9a9a9a;
    --card: #ffffff;
    --backdrop: #e6e6ec;
  }
  * { box-sizing: border-box; margin: 0; padding: 0; }
  html, body {
    width: 1200px; height: 987px; overflow: hidden;
    background: var(--backdrop);
    font-family: "Source Sans 3", "Myriad Pro", Arial, sans-serif;
    color: var(--text);
  }
  .stage { position: relative; width: 1200px; height: 987px; }

  .card {
    position: absolute;
    width: 560px; height: 320px;
    background: var(--card);
    border-radius: 22px;
    overflow: hidden;
    box-shadow: 0 6px 18px rgba(0,0,0,.12);
  }
  .card--back { left: 600px; top: 110px; }
  .card--front { left: 40px; top: 520px; }

  .brand { display: flex; align-items: center; gap: 14px; color: var(--purple); }
  .brand__dot { width: 34px; height: 34px; border-radius: 50%; background: var(--purple); flex: none; }
  .brand__name { font-weight: 600; letter-spacing: 6px; line-height: 1; }

  /* back: appointment */
  .appt { position: absolute; left: 34px; top: 30px; width: 360px; }
  .appt__title { color: var(--purple); font-weight: 700; font-size: 15px; letter-spacing: .5px; margin-bottom: 16px; }
  .appt__row { display: flex; align-items: flex-end; font-size: 15px; margin-bottom: 12px; }
  .appt__line { flex: 1; border-bottom: 1px dotted var(--rule); margin: 0 6px 4px; }
  .appt__hours { font-size: 15px; line-height: 1.3; margin-top: 6px; }
  .appt__note { font-style: italic; font-size: 13.5px; color: #777; margin-top: 8px; }
  .card--back .brand { position: absolute; right: 36px; bottom: 40px; }
  .card--back .brand__name { font-size: 46px; }

  /* front */
  .swoosh { position: absolute; inset: 0; width: 560px; height: 320px; }
  .card--front .brand { position: absolute; left: 34px; top: 58px; }
  .card--front .brand__dot { width: 30px; height: 30px; }
  .card--front .brand__name { font-size: 44px; letter-spacing: 5px; }
  .divider { position: absolute; left: 246px; top: 40px; width: 1px; height: 108px; background: var(--rule); }
  .contact { position: absolute; left: 260px; top: 40px; font-size: 14px; list-style: none; }
  .contact li { display: flex; align-items: center; gap: 6px; margin-bottom: 6px; white-space: nowrap; }
  .contact svg { width: 13px; height: 13px; flex: none; }
  .contact__address { margin-top: 4px; }
  .person { position: absolute; right: 26px; bottom: 16px; text-align: right; color: #fff; }
  .person__name { font-size: 26px; font-weight: 700; line-height: 1.05; }
  .person__title { font-size: 17px; line-height: 1.2; }
</style>
</head>
<body>
<div class="stage">

  <section class="card card--back" aria-label="Appointment card back">
    <div class="appt">
      <h2 class="appt__title">YOUR APPOINTMENT</h2>
      <div class="appt__row">Name :<span class="appt__line"></span></div>
      <div class="appt__row">Date :<span class="appt__line"></span>Time :<span class="appt__line"></span>am / pm</div>
      <p class="appt__hours">Tues - Fri 10am - 8pm Sat 10am–5pm<br>(Appointments required) No walk-ins please.</p>
      <p class="appt__note">We appreciate a 24 hr. notice for cancellations</p>
    </div>
    <div class="brand">
      <span class="brand__dot"></span>
      <span class="brand__name">LUMO</span>
    </div>
  </section>

  <section class="card card--front" aria-label="Business card front">
    <svg class="swoosh" viewBox="0 0 560 320" aria-hidden="true">
      <path d="M0 118 C 40 222, 180 252, 300 232 C 400 216, 470 192, 560 172 L560 320 L0 320 Z" fill="#3d3d3d"/>
      <path d="M0 130 C 40 232, 180 262, 300 242 C 400 226, 470 202, 560 182 L560 320 L0 320 Z" fill="#ffffff"/>
      <path d="M0 140 C 40 240, 180 270, 300 250 C 400 234, 470 210, 560 190 L560 320 L0 320 Z" fill="#662d91"/>
    </svg>
    <div class="brand">
      <span class="brand__dot"></span>
      <span class="brand__name">LUMO</span>
    </div>
    <span class="divider"></span>
    <ul class="contact">
      <li><svg viewBox="0 0 16 16"><circle cx="8" cy="8" r="8" fill="#662d91"/><path d="M5 4.5l1.6-.4 1 2-1 .8c.4 1 1.2 1.8 2.2 2.2l.8-1 2 1-.4 1.6c-3.4 0-6.2-2.8-6.2-6.2z" fill="#fff"/></svg>303.555.0148</li>
      <li><svg viewBox="0 0 16 16"><circle cx="8" cy="8" r="8" fill="#662d91"/><rect x="4" y="5" width="8" height="6" fill="#fff"/><path d="M4 5l4 3.5L12 5" stroke="#662d91" fill="none"/></svg>info@lumobodyworkofdenver.example</li>
      <li><svg viewBox="0 0 16 16"><circle cx="8" cy="8" r="8" fill="#662d91"/><circle cx="8" cy="8" r="4.5" fill="none" stroke="#fff"/><path d="M3.5 8h9M8 3.5v9" stroke="#fff"/></svg>www.lumobodyworkofdenver.example</li>
      <li class="contact__address">2871 E Linden Ave, Denver, CO 80206</li>
    </ul>
    <div class="person">
      <div class="person__name">Your Name</div>
      <div class="person__title">Title</div>
    </div>
  </section>

</div>
</body>
</html>
```